Medical consulting firm needs polished website

I am a physician and working on setting up a smal consulting firm in New Hampshire, USA. It is called Bright Harbor Medical Services, LLC and the website will be BrightHarborMed.com. I was puttering around at making my own website, and it just didn't come together nicely so I've decided to leave it to the pros. The focus of the business is Advanced Care Planning, ie planning for your future medical needs. So it deals with some heavy stuff like planning for if you get sick, who should make decisions for you, end of life options etc. So it can't be too flippant or cutesy, but also can't be too dour and dark. I am hoping to convey that by thinking ahead and making some plans you can lift some of the worries off of yourself and your family - and that we can help make a scary sounding path more manageable. I want it to be made with wordpress and I have actually already bought a template ( Vitarun – A Modern Multidisciplinary Medical & Health Theme ). The website needs to have general information about our services, doc profile, appointment maker, blog/url link page, and ideally web commerce application ( the template has access to woocommerce). I've posted my business card and current brochure (still tweaking them, but you get the idea). I am also partnering with lumenfold.com and so have included their logo and would want connections/info about them. I have the logos etc in different formats as needed.

Target Market(s)

middle aged to older adults

Industry/Entity Type

Medical

Coding

Coded - Design and coding required

Font styles to use
Sans Serif

Requirements
Must have
• as above.
Nice to have
• Ease of reading/access for elderly viewers. woo commerce.

```html
<!DOCTYPE html>
<html lang="en">
<head>
<meta charset="utf-8">
<title>Bright Harbor Medical Services – Advanced Care Planning</title>
<link href="https://fonts.googleapis.com/css2?family=Open+Sans:wght@400;600;700&family=Raleway:wght@500;700&display=swap" rel="stylesheet">
<style>
:root{
  --blue:#1f6fba;
  --blue-band:#2f7fc6;
  --green:#3aa935;
  --ink:#222629;
  --text:#555b60;
  --muted:#8a9096;
  --line:#e3e5e7;
  --grey-bg:#f2f2f2;
  --white:#fff;
}
*{box-sizing:border-box;margin:0;padding:0}
html,body{width:1200px;height:2211px;overflow:hidden}
body{font-family:"Open Sans",Arial,sans-serif;color:var(--text);background:var(--white);position:relative}
.abs{position:absolute}
/* header */
.logo{left:99px;top:30px;display:flex;align-items:center;gap:12px}
.logo-dot{width:46px;height:46px;border-radius:50%;background:var(--blue)}
.logo-name{font-size:22px;font-weight:600;color:var(--blue);line-height:1.15}
.contact{top:38px;display:flex;gap:12px;align-items:center;font-size:11px;line-height:1.5;color:var(--text)}
.contact strong{display:block;color:var(--ink);font-weight:600}
.contact svg{width:32px;height:32px}
.nav{left:99px;top:110px;width:1002px;height:55px;border-top:1px solid var(--line);display:flex;align-items:center}
.nav a{font-size:12px;color:var(--ink);text-decoration:none;padding:0 20px;height:55px;line-height:55px;text-transform:uppercase}
.nav a.active{color:var(--blue);border-top:3px solid var(--blue);margin-top:-1px;line-height:52px}
.nav .tools{margin-left:auto;display:flex;height:55px}
.nav .lang,.nav .search{width:48px;border-left:1px solid var(--line);display:flex;align-items:center;justify-content:center;font-size:12px;color:var(--ink)}
.book{background:var(--blue);color:#fff;font-size:13px;width:220px;display:flex;align-items:center;justify-content:center;gap:8px;text-transform:uppercase}
/* hero */
.hero{left:0;top:165px;width:1200px;height:498px;background:linear-gradient(90deg,#f7f7f7 0%,#eeeeee 40%,#e4e6e8 100%)}
.hero-photo{left:560px;top:165px;width:476px;height:433px;background:linear-gradient(160deg,#d9b89a 0%,#8fb4cf 45%,#4d7ea8 100%)}
.hero-title{left:99px;top:340px;font-family:Raleway,sans-serif;font-weight:700;font-size:28px;color:var(--ink)}
.hero-sub{left:99px;top:383px;font-family:Raleway,sans-serif;font-weight:500;font-size:20px;color:var(--ink)}
.btn{display:inline-flex;align-items:center;justify-content:center;font-size:12px;text-transform:uppercase;height:37px}
.btn-green{background:var(--green);color:#fff;width:103px}
.btn-outline{border:1px solid var(--blue);color:var(--blue);width:101px;background:#fff}
.hero-btns{left:99px;top:435px;display:flex;gap:2px}
.arrow{color:#fff;font-size:30px}
.grey-band{left:0;top:663px;width:1200px;height:538px;background:var(--grey-bg)}
/* features */
.features{left:99px;top:597px;width:1002px;height:195px;background:#fff;display:flex;padding:30px 20px}
.feature{flex:1;padding:0 18px;border-right:1px solid var(--line)}
.feature:last-child{border-right:none}
.feature-head{display:flex;gap:18px;align-items:center;margin-bottom:22px}
.feature-head svg{width:40px;height:40px;flex:none}
.feature h3{font-size:14px;font-weight:600;color:var(--ink);line-height:1.35}
.feature p{font-size:11.5px;color:var(--muted);line-height:1.4}
.slide-dot{width:28px;height:28px;border-radius:50%;background:#d9d9d9;color:#fff;display:flex;align-items:center;justify-content:center;font-size:14px}
/* about */
.about-title{left:99px;top:858px;font-size:31px;font-weight:700;color:var(--ink)}
.about-text{left:99px;top:910px;width:410px;font-size:12px;line-height:1.58;color:var(--ink)}
.about-btn{left:99px;top:1096px;width:101px}
.photo{background:linear-gradient(145deg,#c9d9e8,#e3c3a8 55%,#9bb7d2)}
/* blog */
.blog-title{left:0;top:1255px;width:1200px;text-align:center;font-size:32px;font-weight:700;color:var(--ink)}
.card{top:1338px;width:322px;height:232px;border:1px solid var(--line);padding:20px 18px}
.date{display:inline-block;font-size:12px;color:#fff;background:#bdbdbd;padding:5px 13px}
.date.active{background:var(--blue)}
.card h4{font-size:14px;font-weight:600;color:var(--ink);line-height:1.4;margin:18px 0 12px}
.card p{font-size:12px;line-height:1.5;color:var(--muted)}
.more{margin-top:16px;font-size:12.5px;color:var(--muted);display:flex;align-items:center;gap:8px}
.more.active{color:var(--green)}
.more i{width:12px;height:12px;border-radius:50%;background:currentColor;display:inline-block}
/* stats */
.stats{left:0;top:1636px;width:1200px;height:207px;background:linear-gradient(90deg,#2b78bf,#3584c9 50%,#2c7bc2);display:flex;padding:0 99px}
.stat{flex:1;text-align:center;color:#fff;padding-top:76px;position:relative}
.stat .num{font-size:32px;font-weight:400;position:relative;line-height:1}
.stat .num::before{content:"";position:absolute;left:50%;top:-4px;width:50px;height:40px;margin-left:-25px;background:var(--green);opacity:.55;border-radius:14px;z-index:-1}
.stat .label{font-size:15px;font-weight:600;margin-top:10px;line-height:1.2}
.stat .num span{position:relative}
/* footer */
.f-logo{left:99px;top:1893px;display:flex;align-items:center;gap:8px;font-size:29px;color:#2d5f8e}
.f-logo i{width:24px;height:24px;border-radius:50%;background:#2d5f8e;display:block}
.f-about{left:99px;top:1953px;width:190px;font-size:12px;line-height:1.55;color:var(--ink)}
.f-col{top:1890px;width:232px}
.f-col h5{font-size:19px;font-weight:600;letter-spacing:2px;color:var(--ink);padding-bottom:10px;border-bottom:3px solid var(--ink);margin-bottom:18px}
.f-col ul{list-style:none}
.f-col li{font-size:11px;color:var(--text);line-height:26px}
.f-col p{font-size:11px;line-height:1.5;color:var(--text)}
.subscribe{display:flex;margin-top:18px;height:41px}
.subscribe span{flex:1;border:1px solid var(--line);font-size:11px;color:var(--muted);padding:0 13px;display:flex;align-items:center}
.subscribe b{width:69px;background:var(--green);color:#fff;font-size:12.5px;font-weight:600;display:flex;align-items:center;justify-content:center}
.f-rule{left:99px;top:2147px;width:1002px;border-top:1px solid var(--line)}
.f-copy{left:99px;top:2170px;font-size:10px;color:var(--text)}
.f-legal{right:99px;top:2170px;font-size:10px;color:var(--text);display:flex;gap:16px}
</style>
</head>
<body>

<header>
  <div class="abs logo"><i class="logo-dot"></i><span class="logo-name">Bright Harbor<br>Medical Services</span></div>

  <div class="abs contact" style="left:518px">
    <svg viewBox="0 0 32 32" fill="none" stroke="#333" stroke-width="1.3"><circle cx="16" cy="16" r="14"/><path d="M16 8v8h5"/></svg>
    <div><strong>Monday - Friday 08:00 - 20:00</strong>Saturday and Sunday - CLOSED</div>
  </div>
  <div class="abs contact" style="left:753px">
    <svg viewBox="0 0 32 32" fill="none" stroke="#333" stroke-width="1.3"><circle cx="16" cy="16" r="14"/><rect x="12" y="8" width="8" height="16" rx="1.5"/><path d="M15 21h2"/></svg>
    <div><strong>603-555-0142</strong>For quick contact</div>
  </div>
  <div class="abs contact" style="left:919px">
    <svg viewBox="0 0 32 32" fill="none" stroke="#333" stroke-width="1.3"><circle cx="16" cy="16" r="14"/><rect x="9" y="11" width="14" height="10"/><path d="M9 11l7 6 7-6"/></svg>
    <div><strong>info@brightharbormed.com</strong>Send us mail</div>
  </div>

  <nav class="abs nav">
    <a class="active">Home</a><a>About Us</a><a>Services</a><a>Portfolio</a><a>Blog</a><a>Elements</a><a>Contact Us</a>
    <div class="tools">
      <div class="lang">EN&nbsp;⌄</div>
      <div class="search"><svg width="16" height="16" viewBox="0 0 16 16" fill="none" stroke="#333" stroke-width="1.5"><circle cx="7" cy="7" r="5"/><path d="M11 11l4 4"/></svg></div>
      <div class="book"><svg width="13" height="13" viewBox="0 0 13 13" fill="#fff"><rect x="1" y="2" width="11" height="10" rx="1"/><rect x="2.5" y="5" width="8" height="5.5" fill="#1f6fba"/></svg>Book an appointment</div>
    </div>
  </nav>
</header>

<section>
  <div class="abs hero"></div>
  <div class="abs hero-photo" role="img" aria-label="Smiling family of four standing together in a bright living room"></div>
  <h1 class="abs hero-title">Advanced Care Planning</h1>
  <p class="abs hero-sub">planning for your future medical needs</p>
  <div class="abs hero-btns"><span class="btn btn-green">Read More</span><span class="btn btn-outline">Contact</span></div>
  <div class="abs arrow" style="left:24px;top:388px">‹</div>
  <div class="abs arrow" style="left:1156px;top:388px">›</div>
</section>

<div class="abs grey-band"></div>

<section class="abs features">
  <div class="feature">
    <div class="feature-head">
      <svg viewBox="0 0 40 40" fill="none" stroke="#222" stroke-width="1.4"><circle cx="20" cy="12" r="7"/><path d="M6 38c0-9 6-14 14-14s14 5 14 14z"/><circle cx="15" cy="31" r="2"/></svg>
      <h3>Individualized physician-guided healthcare planning</h3>
    </div>
    <p>Lorem ipsum dolor sit amet, consectetur adipiscing elit. Praesent non metus non lorem lobortis semper quis ut nunc.</p>
  </div>
  <div class="feature">
    <div class="feature-head">
      <svg viewBox="0 0 40 40" fill="none" stroke="#222" stroke-width="1.4"><path d="M36 6L4 17l14 5 5 14z"/></svg>
      <h3>Helping navigate complex medical situations</h3>
    </div>
    <p>Lorem ipsum dolor sit amet, consectetur adipiscing elit. Praesent non metus non lorem lobortis semper quis ut nunc.</p>
  </div>
  <div class="feature">
    <div class="feature-head">
      <svg viewBox="0 0 40 40" fill="none" stroke="#222" stroke-width="1.4"><path d="M12 6l10 10M8 10l10 10M10 8l6-6 10 10-6 6zM19 17l14 14"/><path d="M4 36h18v-4H4z"/></svg>
      <h3>Creating legally binding advanced directives</h3>
    </div>
    <p>Lorem ipsum dolor sit amet, consectetur adipiscing elit. Praesent non metus non lorem lobortis semper quis ut nunc.</p>
  </div>
</section>
<div class="abs slide-dot" style="left:83px;top:679px">‹</div>
<div class="abs slide-dot" style="left:1086px;top:679px">›</div>

<section>
  <h2 class="abs about-title">About Us</h2>
  <p class="abs about-text">Advanced Directives are legally binding documents that spell out what type of medical care you would - or would not - want done to you. We often assume that our families or medical professionals will make "the right decision", but this can be an anguishing process - and often does not accurately reflects the patient's true desires. By making your choices clear, your family and caregivers can honor your wishes when you cannot speak for yourself.</p>
  <span class="abs btn btn-outline about-btn">Read More</span>
  <div class="abs photo" style="left:531px;top:865px;width:278px;height:252px" role="img" aria-label="Father, two children and mother smiling together"></div>
  <div class="abs photo" style="left:822px;top:865px;width:279px;height:252px;background:linear-gradient(145deg,#eef0f2,#e7c7ab 50%,#a9c6e2)" role="img" aria-label="Mother playing with a baby wrapped in a blue towel"></div>
</section>

<section>
  <h2 class="abs blog-title">Latest Blog</h2>
  <article class="abs card" style="left:99px">
    <span class="date active">July 20, 2016</span>
    <h4>Lorem ipsum dolor sit amet, consectetur adipiscing elit.</h4>
    <p>Maecenas eu leo at urna condimentum aliquet. Vivamus iaculis convallis lacus sed viverra. Morbi feugiat nisi eget elementum feugiat.</p>
    <div class="more active">Read More <i></i></div>
  </article>
  <article class="abs card" style="left:439px">
    <span class="date">July 20, 2016</span>
    <h4>Lorem ipsum dolor sit amet, consectetur adipiscing elit.</h4>
    <p>Maecenas eu leo at urna condimentum aliquet. Vivamus iaculis convallis lacus sed viverra. Morbi feugiat nisi eget elementum feugiat.</p>
    <div class="more">Read More <i></i></div>
  </article>
  <article class="abs card" style="left:779px">
    <span class="date">July 20, 2016</span>
    <h4>Lorem ipsum dolor sit amet, consectetur adipiscing elit.</h4>
    <p>Maecenas eu leo at urna condimentum aliquet. Vivamus iaculis convallis lacus sed viverra. Morbi feugiat nisi eget elementum feugiat.</p>
    <div class="more">Read More <i></i></div>
  </article>
</section>

<section class="abs stats" role="img" aria-label="Faded family photograph behind a blue overlay">
  <div class="stat"><div class="num"><span>482</span></div><div class="label">Satishfied Clients</div></div>
  <div class="stat"><div class="num"><span>1482</span></div><div class="label">Lorem ipsum dolor sit<br>amit contan</div></div>
  <div class="stat"><div class="num"><span>435</span></div><div class="label">Dolor sit amit lorem</div></div>
  <div class="stat"><div class="num"><span>12</span></div><div class="label">Cntantry poliar sit</div></div>
</section>

<footer>
  <div class="abs f-logo"><i></i>lumenfold</div>
  <div class="abs f-about">
    <p>Maecenas eu leo at urna condimentum aliquet. Vivamus iaculis convallis lacus sed viverra. Morbi feugiat nisi eget elementum feugiat. Maecenas eu</p>
    <p style="margin-top:16px">eo at urna condimentum aliquet. Vivamus iaculis convallis</p>
  </div>
  <div class="abs f-col" style="left:356px">
    <h5>ABOUT</h5>
    <ul><li>About Us</li><li>Our Mission</li><li>Philosophy</li><li>Principles</li><li>History</li><li>Approach</li></ul>
  </div>
  <div class="abs f-col" style="left:612px">
    <h5>LINKS</h5>
    <ul><li>Campaigns</li><li>Mobile Applications</li><li>Services</li><li>FAQ</li><li>Contact</li></ul>
  </div>
  <div class="abs f-col" style="left:869px">
    <h5>OUR WORKS</h5>
    <p>Lorem ipsum, offers and more. We won't share your address with anyone else.</p>
    <div class="subscribe"><span>Your Email address</span><b>SIGN UP</b></div>
  </div>
  <div class="abs f-rule"></div>
  <div class="abs f-copy">© 2016 Yoursite. All Rights Reserved</div>
  <div class="abs f-legal"><span>Terms of Use</span><span>Privacy Policy</span></div>
</footer>

</body>
</html>
```